Stationery Design Project for Nimbora, Chicago

Nimbora, a street parking application which helps car drivers find a street parking spot by offering an ideal path along which to look for parking. This path is calculated by our algorithm based on data (e.g. historical data, baseball games schedule, etc.). Along this path the driver will find a spot and will also save 70% of the search time. Customer we target is reg. between 21 and 45 yo.

We envision something young, fresh, bright and original. Slightly abstract maybe. It should represent the idea and elements of finding street parking in the city, e.g. car(s), parking spot, people, city, etc. (just ideas!).

Logo is attached.

Requirement:
- Business Cards (2 Sided Full Color CMYK)
- Letterhead (1 Sided Full Color CMYK)
- Envelope (1 Sided Full Color CMYK)
- Sticker (1 Sided Full Color CMYK), round with a 2inch diameter.

Reason: We're starting to get more and more designs and need more time to look into all of them. Very exciting!! Thanks to everybody!

Hi all, we're in the process of selecting our favs. Though choices!!! Really good submissions. Will keep you posted and sorry for the delay.

Target Market(s)

Car drivers and owners between 21 and 45

Industry/Entity Type

Parking

Requirements
Must have
• Sticker should be round and include company URL nimbora.com and the new logo which we will attach soon.
Should not have
• Should not be too serious or boring.

```html
<!DOCTYPE html>
<html lang="en">
<head>
<meta charset="utf-8">
<title>Nimbora Business Card</title>
<link rel="stylesheet" href="https://fonts.googleapis.com/css2?family=Source+Sans+3:wght@400;600;700&display=swap">
<style>
  :root {
    --backdrop: #8c8c8c;
    --card-light: #ffffff;
    --card-light-edge: #d9dadc;
    --ink-dark: #2a2a2a;
    --ink-mid: #555a60;
    --brand-blue: #2b3a96;
    --brand-bright: #1e8fd8;
    --brand-deep: #1b2f8a;
    --white: #ffffff;
  }
  * { margin: 0; padding: 0; box-sizing: border-box; }
  html, body { width: 954px; height: 1200px; overflow: hidden; }
  body {
    background: var(--backdrop);
    font-family: "Source Sans 3", "Myriad Pro", sans-serif;
    position: relative;
  }
  .card {
    position: absolute;
    left: 90px;
    width: 796px;
    height: 454px;
    border-radius: 24px;
    overflow: hidden;
  }
  .card-front {
    top: 91px;
    background: linear-gradient(100deg, var(--card-light) 0%, var(--card-light) 45%, var(--card-light-edge) 100%);
  }
  .card-back {
    top: 658px;
    background: radial-gradient(circle at 50% 40%, var(--brand-bright) 0%, #2467c0 28%, var(--brand-blue) 62%, var(--brand-deep) 100%);
  }
  .brand-mark {
    position: absolute;
    border-radius: 50%;
    background: radial-gradient(circle at 45% 40%, #1aa0e8 0%, #1f5fc4 55%, var(--brand-blue) 100%);
  }
  .card-front .brand-mark { left: 123px; top: 64px; width: 220px; height: 220px; }
  .card-front .brand-name {
    position: absolute;
    left: 66px; top: 304px;
    font-size: 92px; font-weight: 600;
    color: var(--ink-dark);
    letter-spacing: 1px;
    line-height: 1;
  }
  .details { position: absolute; left: 473px; top: 72px; color: var(--ink-mid); font-size: 19px; }
  .person { font-size: 19px; }
  .person-name { font-size: 25px; font-weight: 700; color: #4a4e54; }
  .address { margin-top: 60px; line-height: 33px; }
  .contacts { list-style: none; margin-top: 52px; line-height: 32px; }
  .contacts li { display: flex; align-items: center; gap: 12px; }
  .contacts svg { width: 20px; height: 18px; fill: var(--ink-mid); }
  .card-back .brand-mark {
    left: 283px; top: 82px; width: 210px; height: 210px;
    display: flex; align-items: center; justify-content: center;
  }
  .card-back .brand-name { font-size: 44px; font-weight: 600; color: var(--white); }
  .back-url {
    position: absolute; left: 0; right: 0; top: 382px;
    text-align: center; color: var(--white);
    font-size: 22px; letter-spacing: 4px;
  }
</style>
</head>
<body>
  <section class="card card-front">
    <div class="brand-mark"></div>
    <div class="brand-name">Nimbora</div>
    <div class="details">
      <p class="person"><span class="person-name">Your Name</span> | Designation</p>
      <p class="address">City Name, Street Name<br>State Name, Country Code</p>
      <ul class="contacts">
        <li><svg viewBox="0 0 20 18" aria-hidden="true"><path d="M2 6c0-3 16-3 16 0v2h-4V6H6v2H2z"/><rect x="4" y="9" width="12" height="8" rx="1"/></svg>123-456-7890</li>
        <li><svg viewBox="0 0 20 18" aria-hidden="true"><rect x="5" y="1" width="10" height="5"/><rect x="2" y="6" width="16" height="8" rx="1"/><rect x="5" y="12" width="10" height="5"/></svg>123-456-7890</li>
        <li><svg viewBox="0 0 20 18" aria-hidden="true"><path d="M2 3h16v12H2z M3 4l7 6 7-6" fill="none" stroke="#555a60" stroke-width="1.6"/></svg>name@website.com</li>
        <li><svg viewBox="0 0 20 18" aria-hidden="true"><circle cx="10" cy="9" r="7"/><path d="M3 9h14M10 2c-3 4-3 10 0 14M10 2c3 4 3 10 0 14" fill="none" stroke="#fff" stroke-width="1"/></svg>www.website.com</li>
      </ul>
    </div>
  </section>

  <section class="card card-back">
    <div class="brand-mark"><span class="brand-name">Nimbora</span></div>
    <p class="back-url">www.website.com</p>
  </section>
</body>
</html>
```